Business Cards for IT Consulting Company (Managed Service Provider)

I am looking to have some business cards printed and would like some designs. We are an IT Consulting company based in Vancouver BC. I would like a nice clean and modern look to the cards. I have uploaded all the versions of my logo so parts can be used as needed. Here is a snippit from our website homepage:

Quillbrook Networks Ltd. is an IT Solutions Partner located in Vancouver BC, Canada. We offer IT solutions and support to customers in the greater Vancouver Area. With expertise in Microsoft platforms, as well as Linux and Mac OSX and over 12 years experience in the IT industry, Quillbrook Networks is dedicated to offering our clients top quality service and products. We take pride in the solutions we offer our customers. The greatest compliment a client can give us is to recommend our services.

Quillbrook Networks Ltd. offers a wide range of IT services from onsite service to remote support and managed service solutions. This allows clients to choose the support path that best suits their company’s needs. Supporting many different sized companies from small to enterprise level over the past 12 years Quillbrook Networks has the experience and expertise needed to ensure things run smoothly. Allowing our clients to focus on doing business.

Revolutionizing the way IT services are delivered.

Quillbrook Networks is dedicated to providing our clients with IT solutions that work and grow with them for years to come. This philosophy helps save money in the long run instead of replacing equipment constantly. Far too often IT solutions are not well thought out and while possibly solving the problem at hand, require replacement due to growth or quality within a very short time frame. Quillbrook Networks takes pride in providing solutions that will last and be able to accommodate growth without the need for replacement.

Industry/Entity Type

Information Technology

Contact Information for Business Card

Quillbrook Networks Ltd.
(Employee Name)
Eml: (Employees Email Address)
Web: quillbrook.me
Ph: 604-555-0148

Font styles to use
Serif
Sans Serif

Requirements
Must have
• The Company logo and company colors.
Nice to have
• - Our tag line: "Revolutionizing IT Services" or "Revolutionizing the way IT services are delivered."
• - Also I really like the idea of nature and technology together blending which is sort of where my logo came from so integrating that somehow onto the business cards would be great.

```html
<!DOCTYPE html>
<html lang="en">
<head>
<meta charset="utf-8">
<title>Quillbrook Networks – Business Cards</title>
<link href="https://fonts.googleapis.com/css2?family=Montserrat:wght@400;500;600;700&display=swap" rel="stylesheet">
<style>
  :root {
    --backdrop: #2b2b2d;
    --card: #050505;
    --brand-blue: #1ba6ea;
    --ink-white: #ffffff;
    --ink-soft: #d9d9d9;
  }
  * { margin: 0; padding: 0; box-sizing: border-box; }
  html, body {
    width: 1200px; height: 900px; overflow: hidden;
    background: var(--backdrop);
    font-family: "Montserrat", sans-serif;
  }
  .stage { position: relative; width: 1200px; height: 900px; }
  .card {
    position: absolute;
    width: 560px; height: 320px;
    background: var(--card);
    border-radius: 20px;
    overflow: hidden;
  }
  .card--front { left: 130px; top: 110px; }
  .card--back  { left: 510px; top: 470px; }

  /* Front */
  .front-brand {
    position: absolute; left: 0; right: 0; top: 110px;
    display: flex; align-items: center; justify-content: center; gap: 14px;
  }
  .brand-square {
    width: 30px; height: 30px; background: var(--brand-blue);
  }
  .front-brand .brand-name {
    color: var(--brand-blue); font-weight: 600; font-size: 28px; letter-spacing: 0.5px;
  }
  .tagline {
    position: absolute; left: 0; right: 0; top: 232px;
    text-align: center; color: var(--ink-soft);
    font-size: 14px; font-weight: 500; letter-spacing: 1.2px;
  }

  /* Back */
  .back-brand {
    position: absolute; left: 38px; top: 50px;
    display: flex; align-items: center; gap: 16px;
  }
  .back-brand .brand-square { width: 44px; height: 44px; }
  .back-brand .brand-name {
    color: var(--brand-blue); font-weight: 600; font-size: 30px; line-height: 1.05;
  }
  .rule {
    position: absolute; left: 38px; right: 38px; top: 190px;
    height: 2px; background: var(--brand-blue);
  }
  .person-name {
    position: absolute; left: 38px; top: 160px;
    color: var(--brand-blue); font-weight: 700; font-size: 20px; letter-spacing: 1.5px;
  }
  .person-role {
    position: absolute; left: 38px; top: 200px;
    color: var(--ink-white); font-weight: 600; font-size: 13px; letter-spacing: 1px;
  }
  .contact-list {
    position: absolute; left: 38px; top: 226px;
    list-style: none;
  }
  .contact-list li {
    display: flex; align-items: center; gap: 10px;
    color: var(--ink-white); font-size: 14px; font-weight: 500; letter-spacing: 0.6px;
    height: 24px;
  }
  .contact-list svg { width: 12px; height: 12px; flex: none; }
</style>
</head>
<body>
<main class="stage">

  <section class="card card--front" aria-label="Card front">
    <div class="front-brand">
      <span class="brand-square" aria-hidden="true"></span>
      <span class="brand-name">Quillbrook Networks Ltd.</span>
    </div>
    <p class="tagline">Revolutionizing IT Services</p>
  </section>

  <section class="card card--back" aria-label="Card back">
    <div class="back-brand">
      <span class="brand-square" aria-hidden="true"></span>
      <span class="brand-name">Quillbrook<br>Networks Ltd.</span>
    </div>

    <h2 class="person-name">MAREK HALDEN</h2>
    <div class="rule" aria-hidden="true"></div>
    <p class="person-role">DIRECTOR</p>

    <ul class="contact-list">
      <li>
        <svg viewBox="0 0 12 12" aria-hidden="true"><path d="M2.5 1h2l1 2.5-1.3 1a6 6 0 0 0 3.3 3.3l1-1.3L11 7.5v2a1 1 0 0 1-1 1A9 9 0 0 1 1.5 2a1 1 0 0 1 1-1z" fill="#1ba6ea"/></svg>
        604-555-0148
      </li>
      <li>
        <svg viewBox="0 0 12 12" aria-hidden="true"><rect x="1" y="2.5" width="10" height="7" rx="1" fill="none" stroke="#1ba6ea" stroke-width="1.2"/><path d="M1.5 3l4.5 3.5L10.5 3" fill="none" stroke="#1ba6ea" stroke-width="1.2"/></svg>
        info@marekhalden.com
      </li>
      <li>
        <svg viewBox="0 0 12 12" aria-hidden="true"><circle cx="6" cy="6" r="5" fill="none" stroke="#1ba6ea" stroke-width="1.2"/><path d="M1 6h10M6 1c-2 2.5-2 7.5 0 10M6 1c2 2.5 2 7.5 0 10" fill="none" stroke="#1ba6ea" stroke-width="1"/></svg>
        www.quillbrook.me
      </li>
    </ul>
  </section>

</main>
</body>
</html>
```